Four in One (Flexible infographic for Content Management Industry)

See attachment.
A graphic depicting 4 products, where each can stand on its own and each can be combined with others, but where, if all are taken together, the best result is achieved (the "super product").
Intended use is web. See attached file as an example.
The most basic idea is as the attached diagram shows, where 4 rectangles are arranged in a quadrangle, with a middle rectangle in the center representing the combined 4 products. This concept is fine except it is a bit too obvious as it stands. We are looking for either a variation of this or another concept.
The audience is technical + professional + enterprise - NOT consumers. Hence the design should be conservative in nature.
We are aware of tools like as Canva or Pictogram where such graphics are available, but we are looking for something with a bit more imagination and flexibility.
This graphic should be targeted to web sites and be delivered with vector-based (SVG) graphics.

```html
<!DOCTYPE html>
<html lang="en">
<head>
<meta charset="utf-8">
<title>Super Product – Four in One</title>
<link rel="stylesheet" href="https://fonts.googleapis.com/css2?family=Montserrat:wght@400;600;700&display=swap">
<style>
  :root {
    --ring: #9c4795;
    --doc: #e2af20;
    --security: #1c7898;
    --erp: #9dc03a;
    --digital: #129682;
    --ink: #ffffff;
    --page: #ffffff;
  }
  * { margin: 0; padding: 0; box-sizing: border-box; }
  html, body { width: 1200px; height: 675px; overflow: hidden; background: var(--page); }
  body { font-family: "Montserrat", Arial, sans-serif; color: var(--ink); }
  .canvas { position: relative; width: 1200px; height: 675px; }
  .diagram { position: absolute; inset: 0; }
  .ring-title { font-family: "Montserrat", Arial, sans-serif; font-weight: 700; font-size: 25px; fill: var(--ink); }

  .module { position: absolute; width: 230px; white-space: nowrap; }
  .module-title { font-weight: 700; font-size: 10.6px; line-height: 12px; margin-bottom: 3px; }
  .module-text { font-size: 9px; line-height: 10px; margin-bottom: 4px; letter-spacing: -0.05px; }
  .module-list { list-style: none; font-size: 9px; line-height: 14.4px; }
  .module-list li::before { content: "· "; }
  .learn-more { display: inline-block; font-weight: 600; font-size: 10.6px; line-height: 14px; color: var(--ink); text-decoration: none; }
  .learn-more::after { content: " ▸"; font-size: 7px; vertical-align: 1px; }

  .module--doc { left: 364px; top: 206px; }
  .module--security { left: 630px; top: 206px; }
  .module--erp { left: 362px; top: 361px; }
  .module--digital { left: 630px; top: 361px; }
</style>
</head>
<body>
<main class="canvas">
  <svg class="diagram" width="1200" height="675" viewBox="0 0 1200 675" aria-hidden="true">
    <defs>
      <path id="ring-arc" d="M 310,337.5 A 290,290 0 0 1 890,337.5"/>
    </defs>
    <circle class="ring" cx="600" cy="340" r="333" fill="var(--ring)"/>
    <text class="ring-title"><textPath href="#ring-arc" startOffset="50%" text-anchor="middle">Super Product</textPath></text>

    <g stroke-linejoin="round" stroke-width="4">
      <path class="quadrant quadrant--doc" fill="var(--doc)" stroke="var(--doc)" d="M584,62 L584,320 L324.5,320 A276,276 0 0 1 584,62 Z"/>
      <path class="quadrant quadrant--security" fill="var(--security)" stroke="var(--security)" d="M617,62 L617,320 L875.5,320 A276,276 0 0 0 617,62 Z"/>
      <path class="quadrant quadrant--erp" fill="var(--erp)" stroke="var(--erp)" d="M584,354.5 L584,612 A276,276 0 0 1 324.5,354.5 Z"/>
      <path class="quadrant quadrant--digital" fill="var(--digital)" stroke="var(--digital)" d="M617,354.5 L617,612 A276,276 0 0 0 875.5,354.5 Z"/>
    </g>

    <g class="icon icon--doc">
      <path d="M536,85 H557 L569,97 V129 a3,3 0 0 1 -3,3 H536 a3,3 0 0 1 -3,-3 V88 a3,3 0 0 1 3,-3 Z" fill="var(--ink)"/>
      <path d="M558,85 L569,96 H558 Z" fill="var(--doc)"/>
      <path d="M559,85 V95 H569" fill="none" stroke="var(--doc)" stroke-width="2"/>
      <g stroke="var(--doc)" stroke-width="2.2" stroke-linecap="round">
        <line x1="541" y1="104" x2="561" y2="104"/>
        <line x1="541" y1="112" x2="561" y2="112"/>
        <line x1="541" y1="119" x2="548" y2="119"/>
      </g>
    </g>

    <g class="icon icon--cloud">
      <path d="M640,124 a10,10 0 0 1 -1,-20 a14,14 0 0 1 27,-5 a11,11 0 0 1 1,22 Z" fill="var(--ink)"/>
      <path d="M641,109 L646,115 L656,103" fill="none" stroke="var(--security)" stroke-width="3.2" stroke-linecap="round" stroke-linejoin="round"/>
    </g>

    <g class="icon icon--apps" fill="var(--ink)">
      <rect x="522" y="539" width="21" height="20" rx="4"/>
      <rect x="522" y="563" width="21" height="21" rx="4"/>
      <rect x="546" y="563" width="21" height="21" rx="4"/>
      <rect x="547" y="540" width="17" height="17" rx="3" transform="rotate(45 555.5 548.5)"/>
    </g>

    <g class="icon icon--search">
      <rect x="630" y="536" width="46" height="47" rx="6" fill="var(--ink)"/>
      <circle cx="650" cy="556" r="9" fill="none" stroke="var(--digital)" stroke-width="3.2"/>
      <line x1="657" y1="563" x2="665" y2="571" stroke="var(--digital)" stroke-width="3.6" stroke-linecap="round"/>
    </g>
  </svg>

  <section class="module module--doc">
    <h2 class="module-title">Document Management</h2>
    <p class="module-text">Streamline document organization, access, and<br>collaboration with easier file storage and<br>sharing, leading to more efficient workflows.</p>
    <ul class="module-list">
      <li>Centralized Document Control</li>
      <li>Collaborative Workspace Integration</li>
      <li>Automated Compliance Tracking</li>
    </ul>
    <a class="learn-more" href="#">Learn More</a>
  </section>

  <section class="module module--security">
    <h2 class="module-title">Security and Compliance</h2>
    <p class="module-text">Benefit from tailored cloud solutions, secure<br>data storage, and expert disaster recovery<br>planning for reliable and scalable IT operations.</p>
    <ul class="module-list">
      <li>Custom Cloud Solutions</li>
      <li>Secure Data Storage</li>
      <li>Expert Disaster Recovery</li>
    </ul>
    <a class="learn-more" href="#">Learn More</a>
  </section>

  <section class="module module--erp">
    <h2 class="module-title">Enterprise Resource Planning</h2>
    <p class="module-text">Simplify management across finance, sales, and<br>operations, enabling better decision-making<br>and improved productivity.</p>
    <ul class="module-list">
      <li>Integrated Business Processes</li>
      <li>Enhanced Decision-Making</li>
      <li>Productivity Improvement</li>
    </ul>
    <a class="learn-more" href="#">Learn More</a>
  </section>

  <section class="module module--digital">
    <h2 class="module-title">Digitital Transformation</h2>
    <p class="module-text">Turn scanned documents into easily searchable<br>digital archives, boosting efficiency and<br>accessibility.</p>
    <ul class="module-list">
      <li>Instant searchable Archives with OCR</li>
      <li>Automated Document Classification</li>
      <li>DeskHub and Cloud Blob Ready</li>
    </ul>
    <a class="learn-more" href="#">Learn More</a>
  </section>
</main>
</body>
</html>
```